Music Industry Business Needs a Business Card Design

Copper Lantern is an audio mastering company that has been in business for 20 years. Mastering is the final creative step in the music production chain. Our job is to make the music sound as good as it possibly can prior to release to the public. Our world is technical, artistic, precise. We work on everything from independent artists to the music for the Grandfield Cup. We are looking for a new, more modern business card design. I am uploading a copy of our logo, although it doesn't absolutely need to be included in the design.

Target Market(s)

Music Industry Professionals

Industry/Entity Type

Business

Contact Information for Business Card

Address, Phone, Email, Website, Name, Job Title

Font styles to use
Sans Serif

Requirements
Must have
• Sorry, but I don't have any concrete things to request. If I had a clear idea of what I want, I would probably just design something myself. I am looking for fresh input and thought I would try this.
Should not have
• Anything that is typical, such as headphones or the like.

```html
<!DOCTYPE html>
<html lang="en">
<head>
<meta charset="utf-8">
<title>Copper Lantern – Business Card</title>
<link rel="stylesheet" href="https://fonts.googleapis.com/css2?family=Questrial&display=swap">
<style>
  :root {
    --canvas: #d3d8d3;
    --card-dark: #141414;
    --card-dark-2: #2c2d2f;
    --band-white: #ffffff;
    --accent-orange: #f7931e;
    --ink: #1a1a1a;
    --light-text: #e9e9e9;
    --icon-grey: #3c3f44;
    --line-yellow: #f4e04d;
    --line-orange: #f7931e;
    --line-red: #e8261c;
    --line-purple: #6a1fd0;
  }
  * { margin: 0; padding: 0; box-sizing: border-box; }
  html, body {
    width: 1200px; height: 1000px; overflow: hidden;
    background: var(--canvas);
    font-family: "Questrial", "Century Gothic", sans-serif;
  }
  .stage {
    width: 1200px; height: 1000px;
    display: flex; align-items: center; justify-content: center;
  }
  .business-card {
    position: relative;
    width: 1000px; height: 572px;
    background: linear-gradient(160deg, var(--card-dark-2) 0%, var(--card-dark) 45%, var(--card-dark-2) 100%);
    box-shadow: 0 18px 40px rgba(0,0,0,0.35);
    overflow: hidden;
  }
  .card-art { position: absolute; inset: 0; }
  .brand-name {
    position: absolute; left: 300px; top: 70px;
    color: var(--accent-orange);
    font-size: 40px; letter-spacing: 3px;
    text-transform: uppercase;
  }
  .holder {
    position: absolute; right: 70px; top: 200px; text-align: right;
  }
  .holder-name { color: var(--accent-orange); font-size: 44px; font-weight: 400; }
  .holder-title { color: var(--light-text); font-size: 26px; letter-spacing: 1px; margin-top: 4px; }
  .contact-list {
    position: absolute; left: 300px; top: 300px;
    list-style: none; color: var(--ink);
  }
  .contact-list li {
    display: flex; align-items: center; gap: 18px;
    font-size: 30px; height: 42px;
  }
  .contact-list svg { width: 34px; height: 30px; flex: none; }
  .website {
    position: absolute; left: 56px; bottom: 28px;
    color: var(--light-text); font-size: 38px; letter-spacing: 1.5px;
  }
</style>
</head>
<body>
<main class="stage">
  <article class="business-card">
    <svg class="card-art" viewBox="0 0 1000 572" width="1000" height="572" aria-hidden="true">
      <defs>
        <linearGradient id="edge-top" x1="0" y1="0" x2="1" y2="0">
          <stop offset="0" stop-color="var(--line-purple)"/>
          <stop offset="0.45" stop-color="var(--line-red)"/>
          <stop offset="0.75" stop-color="var(--line-orange)"/>
          <stop offset="1" stop-color="var(--line-yellow)"/>
        </linearGradient>
        <linearGradient id="edge-bottom" x1="0" y1="0" x2="1" y2="0">
          <stop offset="0" stop-color="var(--line-red)"/>
          <stop offset="0.5" stop-color="var(--line-orange)"/>
          <stop offset="1" stop-color="var(--line-yellow)"/>
        </linearGradient>
      </defs>
      <path class="white-band" fill="var(--band-white)"
            d="M0 150 C 320 210, 700 300, 1000 420 L 1000 540 C 650 470, 300 440, 0 410 Z"/>
      <path fill="none" stroke="url(#edge-top)" stroke-width="4"
            d="M0 150 C 320 210, 700 300, 1000 420"/>
      <path fill="none" stroke="url(#edge-bottom)" stroke-width="4"
            d="M0 410 C 300 440, 650 470, 1000 540"/>
    </svg>

    <div class="brand-name">Copper Lantern</div>

    <div class="holder">
      <div class="holder-name">Mara Ellison</div>
      <div class="holder-title">manager</div>
    </div>

    <ul class="contact-list">
      <li>
        <svg viewBox="0 0 34 30"><ellipse cx="17" cy="15" rx="15" ry="11" fill="none" stroke="var(--accent-orange)" stroke-width="4"/><circle cx="17" cy="15" r="5" fill="var(--icon-grey)"/></svg>
        <span>555 310 4477</span>
      </li>
      <li>
        <svg viewBox="0 0 34 30"><path d="M17 2 L32 15 H27 V28 H7 V15 H2 Z" fill="var(--accent-orange)"/></svg>
        <span>48 Harbor Lane</span>
      </li>
      <li>
        <svg viewBox="0 0 34 30"><rect x="2" y="5" width="30" height="20" rx="2" fill="var(--icon-grey)"/><path d="M3 6 L17 17 L31 6" fill="none" stroke="#fff" stroke-width="2"/></svg>
        <span>info@copperlantern.com</span>
      </li>
    </ul>

    <div class="website">www.copperlantern.com</div>
  </article>
</main>
</body>
</html>
```